Kestrel Facilities Business Card Design

We would now like to design business cards with the new Kestrel Facilities logo

Target Market(s)

Professional

Industry/Entity Type

Professional services

Contact Information for Business Card

Employee name, title, phone number, email address, corporate office address and logo.

Font styles to use
Sans Serif

Colors
0054AA
0677BA
7BADD7
CADEEF
E8F1F8

Requirements
Must have
• My logo
Should not have
• any other pictures or images besides my logo

```html
<!DOCTYPE html>
<html lang="en">
<head>
<meta charset="utf-8">
<title>Kestrel Facilities Business Card</title>
<link href="https://fonts.googleapis.com/css2?family=Oswald:wght@400;500&family=Arimo:wght@400&display=swap" rel="stylesheet">
<style>
  :root {
    --backdrop: #232323;
    --brand-blue: #0680e8;
    --brand-deep: #0054aa;
    --paper: #ffffff;
    --ink: #111111;
  }
  html, body {
    margin: 0;
    padding: 0;
    width: 1075px;
    height: 1200px;
    overflow: hidden;
    background: var(--backdrop);
  }
  .canvas {
    position: relative;
    width: 1075px;
    height: 1200px;
  }
  .card {
    position: absolute;
    left: 206px;
    width: 663px;
    height: 395px;
    overflow: hidden;
  }
  .card--front { top: 187px; background: var(--paper); }
  .card--back  { top: 637px; background: var(--brand-blue); }

  .holder {
    position: absolute;
    left: 29px;
    top: 86px;
    font-family: "Arimo", Arial, sans-serif;
    color: var(--ink);
  }
  .holder__name {
    margin: 0;
    font-family: "Oswald", "Arial Narrow", sans-serif;
    font-weight: 400;
    font-size: 30px;
    line-height: 1;
    color: var(--brand-blue);
    letter-spacing: -0.3px;
  }
  .holder__title {
    margin: 3px 0 0;
    font-size: 19.5px;
  }
  .contact {
    list-style: none;
    margin: 22px 0 0;
    padding: 0;
    font-size: 19.5px;
    line-height: 23.5px;
  }
  .contact li { display: flex; align-items: center; gap: 6px; }
  .contact svg { width: 17px; height: 17px; flex: none; }
  .contact .accent { color: var(--brand-blue); }
  .address {
    margin: 22px 0 0;
    font-size: 19.5px;
    line-height: 24px;
  }

  .brand-panel {
    position: absolute;
    left: 276px;
    top: 0;
    width: 387px;
    height: 395px;
    display: flex;
    align-items: center;
    justify-content: center;
    gap: 14px;
  }
  .brand-mark {
    width: 34px;
    height: 34px;
    background: var(--brand-blue);
  }
  .brand-name {
    font-family: "Oswald", "Arial Narrow", sans-serif;
    font-weight: 500;
    font-size: 40px;
    line-height: 1.05;
    color: var(--brand-blue);
    text-transform: uppercase;
  }

  .back-brand {
    position: absolute;
    inset: 0;
    display: flex;
    align-items: center;
    justify-content: center;
    gap: 16px;
  }
  .back-brand .brand-mark { background: var(--brand-deep); }
  .back-brand .brand-name { color: var(--brand-deep); font-size: 46px; }
</style>
</head>
<body>
<main class="canvas">
  <section class="card card--front" aria-label="Business card front">
    <div class="holder">
      <h1 class="holder__name">DANIEL HAYES</h1>
      <p class="holder__title">Managing Director</p>
      <ul class="contact">
        <li>
          <svg viewBox="0 0 24 24" aria-hidden="true"><path fill="#0680e8" d="M6.6 10.8a15 15 0 0 0 6.6 6.6l2.2-2.2c.3-.3.7-.4 1-.2 1.1.4 2.3.6 3.6.6.6 0 1 .4 1 1V20c0 .6-.4 1-1 1A17 17 0 0 1 3 4c0-.6.4-1 1-1h3.5c.6 0 1 .4 1 1 0 1.3.2 2.5.6 3.6.1.3 0 .7-.2 1z"/></svg>
          <span>055-204 318 467</span>
        </li>
        <li>
          <svg viewBox="0 0 24 24" aria-hidden="true"><rect x="2" y="5" width="20" height="14" fill="#0680e8"/><path d="M2 5l10 8 10-8" fill="none" stroke="#fff" stroke-width="1.6"/></svg>
          <span>info@kestrelmail.com</span>
        </li>
        <li>
          <svg viewBox="0 0 24 24" aria-hidden="true"><g fill="none" stroke="#0680e8" stroke-width="1.8"><circle cx="12" cy="12" r="9"/><ellipse cx="12" cy="12" rx="4" ry="9"/><path d="M3 12h18M5 7h14M5 17h14"/></g></svg>
          <span>www.<span class="accent">kestrelfacilities</span>.com</span>
        </li>
      </ul>
      <p class="address">218, Harbour View Road<br>Westbrook 40718, Avalon</p>
    </div>
    <div class="brand-panel">
      <span class="brand-mark" aria-hidden="true"></span>
      <span class="brand-name">Kestrel<br>Facilities</span>
    </div>
  </section>

  <section class="card card--back" aria-label="Business card back">
    <div class="back-brand">
      <span class="brand-mark" aria-hidden="true"></span>
      <span class="brand-name">Kestrel<br>Facilities</span>
    </div>
  </section>
</main>
</body>
</html>
```